PYLON SIGN FOR “MEADOWLARK CAR WASH SPRINT”

please see the new images in my brief. I have a logo design and the colors I would like you to follow.

please put "meadowlark car wash sprint" in the logo

Target Market(s)

GENERAL PUBLIC

Industry/Entity Type

CAR WASH

Font styles to use
Other font styles liked:
• CURSIVE AND BLOCK LETTERING BOTH AS IN THE SAMPLE PIC

Colors
00AB8E
00BBA5
67D7C9
C6EFE9
E9F9F6
6B429C
8869AF
B7A5CE
E3DAEB
F3F0F8

Requirements
Must have
• 1. “MEADOWLARK CAR WASH SPRINT” PLEASE PUT THIS IN THE LOGO 2. USE BLACK, WHITE, GREEN AND SILVER FOR A COLOR
Nice to have
• I WOULD LIKE TO SEE THE SIGN IN BOTH COLOR THEMES: WHITE, BLACK, GREEN AND SILVER AND WHITE BLACK PURPLE AND SILVER

```html
<!DOCTYPE html>
<html lang="en">
<head>
<meta charset="utf-8">
<title>Meadowlark Car Wash Sprint – Pylon Sign</title>
<link rel="stylesheet" href="https://fonts.googleapis.com/css2?family=Montserrat:wght@300;800&display=swap">
<style>
  :root {
    --page-bg: #c8c8c8;
    --sign-bg: #1c1a1b;
    --green-light: #9be22d;
    --green-dark: #55a80f;
    --silver-light: #f2f2f2;
    --silver-dark: #a9a9a9;
    --white: #ffffff;
    --foam: #8c8c8c;
  }
  html, body {
    margin: 0;
    padding: 0;
    width: 830px;
    height: 1200px;
    overflow: hidden;
    background: var(--page-bg);
  }
  .canvas {
    width: 830px;
    height: 1200px;
    display: flex;
    align-items: center;
    justify-content: center;
  }
  .pylon-sign {
    display: block;
    width: 770px;
    height: 588px;
    box-shadow: 0 12px 28px rgba(0, 0, 0, 0.35);
  }
  .headline {
    font-family: "Montserrat", Arial, sans-serif;
  }
  .headline--heavy { font-weight: 800; }
  .headline--light { font-weight: 300; }
</style>
</head>
<body>
<main class="canvas">
  <svg class="pylon-sign" viewBox="0 0 1051 802" xmlns="http://www.w3.org/2000/svg" aria-label="Meadowlark Car Wash Sprint pylon sign">
    <defs>
      <linearGradient id="green-fill" x1="0" y1="0" x2="0" y2="1">
        <stop offset="0" stop-color="var(--green-light)"/>
        <stop offset="0.55" stop-color="var(--green-light)"/>
        <stop offset="0.56" stop-color="var(--green-dark)"/>
        <stop offset="1" stop-color="var(--green-dark)"/>
      </linearGradient>
      <linearGradient id="silver-fill" x1="0" y1="0" x2="0" y2="1">
        <stop offset="0" stop-color="var(--silver-light)"/>
        <stop offset="0.5" stop-color="var(--silver-light)"/>
        <stop offset="0.51" stop-color="var(--silver-dark)"/>
        <stop offset="1" stop-color="#d6d6d6"/>
      </linearGradient>
      <radialGradient id="car-glow" cx="0.5" cy="0.6" r="0.6">
        <stop offset="0" stop-color="var(--silver-dark)" stop-opacity="0.35"/>
        <stop offset="1" stop-color="var(--silver-dark)" stop-opacity="0"/>
      </radialGradient>
      <linearGradient id="foam-fill" x1="0" y1="0" x2="0" y2="1">
        <stop offset="0" stop-color="var(--foam)" stop-opacity="0"/>
        <stop offset="0.5" stop-color="var(--foam)" stop-opacity="0.5"/>
        <stop offset="1" stop-color="var(--foam)" stop-opacity="0.85"/>
      </linearGradient>
    </defs>

    <rect class="sign-panel" width="1051" height="802" fill="var(--sign-bg)"/>

    <rect class="car-silhouette" x="40" y="60" width="970" height="160" rx="80" fill="url(#car-glow)" role="img" aria-label="Silver swooping sports car outline"/>

    <rect class="soap-foam" x="0" y="560" width="1051" height="242" fill="url(#foam-fill)" role="img" aria-label="Soap bubbles and foam along the bottom edge"/>

    <text class="headline headline--heavy" x="122" y="312" font-size="130" textLength="803" lengthAdjust="spacingAndGlyphs" fill="url(#green-fill)">MEADOWLARK</text>
    <text class="headline headline--heavy" x="86" y="445" font-size="165" textLength="879" lengthAdjust="spacingAndGlyphs" fill="url(#silver-fill)">CAR WASH</text>
    <text class="headline headline--light" x="190" y="572" font-size="150" textLength="665" lengthAdjust="spacingAndGlyphs" fill="var(--white)">SPRINT</text>

    <g class="brand-mark">
      <circle cx="330" cy="728" r="10" fill="var(--green-light)"/>
      <text class="headline headline--heavy" x="352" y="738" font-size="28" textLength="390" lengthAdjust="spacingAndGlyphs" fill="var(--green-light)">MEADOWLARK CAR WASH SPRINT</text>
    </g>
  </svg>
</main>
</body>
</html>
```